Veltrano.co - Polar Expeditions Specialists

We need a modern, visually striking business card for Veltrano.co, a company specialized in selling expedition cruises to the most remote regions on Earth, with a focus on the Arctic and Antarctica. The design should instantly communicate that the cardholder is an expert in polar travel. Use clean, premium aesthetics with cool tones like icy blue and white, possibly incorporating polar imagery (ice, glaciers, penguins, etc.)

Attached the logo

Contact Information for Business Card

Feels high-end and trustworthy.. Visually memorable — encourages people to keep it

Colors
0054AA
0677BA
7BADD7
CADEEF
E8F1F8

Requirements
Must have
• ice, glaciers, penguins, montains
Nice to have
• modern, transparente,

```html
<!DOCTYPE html>
<html lang="en">
<head>
<meta charset="UTF-8">
<title>Veltrano.co – Business Card</title>
<link rel="stylesheet" href="https://fonts.googleapis.com/css2?family=Poppins:wght@300;400;500;600;700&display=swap">
<style>
  :root {
    --page-bg: #e3e8ea;
    --navy-top: #323a57;
    --navy-mid: #2a3350;
    --navy-deep: #172140;
    --ice-haze: rgba(123, 173, 215, 0.14);
    --white: #ffffff;
    --divider: rgba(255, 255, 255, 0.55);
  }
  * { box-sizing: border-box; margin: 0; padding: 0; }
  html, body {
    width: 1200px; height: 960px; overflow: hidden;
    background: var(--page-bg);
    font-family: "Poppins", sans-serif;
    color: var(--white);
  }
  .card {
    position: absolute; left: 250px;
    width: 700px; height: 400px;
    border-radius: 24px; overflow: hidden;
  }
  .card--front { top: 60px; }
  .card--back { top: 500px; }

  .card__scenery {
    position: absolute; inset: 0;
    background:
      radial-gradient(ellipse 70% 30% at 45% 62%, var(--ice-haze), transparent 70%),
      linear-gradient(180deg, var(--navy-top) 0%, var(--navy-mid) 55%, var(--navy-deep) 100%);
  }

  .brand { position: absolute; left: 0; right: 0; text-align: center; }
  .brand__dot {
    display: block; margin: 0 auto;
    border-radius: 50%; background: var(--white);
  }
  .brand__name { font-weight: 700; line-height: 1; letter-spacing: -0.5px; }
  .brand__tagline { font-weight: 600; }

  .card--front .brand { top: 100px; }
  .card--front .brand__dot { width: 60px; height: 60px; margin-bottom: 72px; }
  .card--front .brand__name { font-size: 76px; }
  .card--front .brand__tagline { font-size: 21px; margin-top: 14px; }

  .card--back .brand { top: 118px; width: 350px; }
  .card--back .brand__dot { width: 44px; height: 44px; margin-bottom: 56px; }
  .card--back .brand__name { font-size: 48px; }
  .card--back .brand__tagline { font-size: 15px; margin-top: 8px; }

  .divider {
    position: absolute; left: 350px; top: 80px;
    width: 1px; height: 240px; background: var(--divider);
  }

  .person { position: absolute; left: 408px; top: 114px; }
  .person__name { font-size: 33px; line-height: 1; letter-spacing: 0.5px; }
  .person__first { font-weight: 600; }
  .person__last { font-weight: 300; }
  .person__role { font-size: 17px; font-weight: 500; margin-top: 6px; }

  .contacts { position: absolute; left: 408px; top: 206px; list-style: none; }
  .contacts__item {
    display: flex; align-items: center; gap: 10px;
    height: 26px; font-size: 19px; font-weight: 400; letter-spacing: 0.3px;
  }
  .contacts__icon { width: 17px; height: 17px; flex: none; }

  .address {
    position: absolute; left: 0; right: 0; top: 346px;
    text-align: center; font-size: 18px; font-weight: 400; letter-spacing: 0.4px;
  }
</style>
</head>
<body>

<section class="card card--front">
  <div class="card__scenery" role="img" aria-label="Dark navy-tinted photo of icebergs and glaciers over calm polar water"></div>
  <div class="brand">
    <span class="brand__dot"></span>
    <div class="brand__name">Veltrano.co</div>
    <div class="brand__tagline">Polar Expeditions Specialists</div>
  </div>
</section>

<section class="card card--back">
  <div class="card__scenery" role="img" aria-label="Dark navy-tinted photo of icebergs and glaciers over calm polar water"></div>
  <div class="brand">
    <span class="brand__dot"></span>
    <div class="brand__name">Veltrano.co</div>
    <div class="brand__tagline">Polar Expeditions Specialists</div>
  </div>

  <div class="divider"></div>

  <div class="person">
    <div class="person__name"><span class="person__first">Marta</span> <span class="person__last">Lindqvist</span></div>
    <div class="person__role">Founder &amp; CEO</div>
  </div>

  <ul class="contacts">
    <li class="contacts__item">
      <svg class="contacts__icon" viewBox="0 0 24 24" fill="none" stroke="#fff" stroke-width="2" stroke-linecap="round" stroke-linejoin="round"><path d="M22 16.9v3a2 2 0 0 1-2.2 2 19.8 19.8 0 0 1-8.6-3.1 19.5 19.5 0 0 1-6-6A19.8 19.8 0 0 1 2.1 4.2 2 2 0 0 1 4.1 2h3a2 2 0 0 1 2 1.7c.1 1 .4 1.9.7 2.8a2 2 0 0 1-.5 2.1L8 9.9a16 16 0 0 0 6 6l1.3-1.3a2 2 0 0 1 2.1-.4c.9.3 1.8.6 2.8.7a2 2 0 0 1 1.8 2z"/></svg>
      <span>(555) 214-0386</span>
    </li>
    <li class="contacts__item">
      <svg class="contacts__icon" viewBox="0 0 24 24" fill="none" stroke="#fff" stroke-width="2"><circle cx="12" cy="12" r="10"/><path d="M2 12h20M12 2a15 15 0 0 1 0 20M12 2a15 15 0 0 0 0 20"/></svg>
      <span>hello@veltrano.co</span>
    </li>
    <li class="contacts__item">
      <svg class="contacts__icon" viewBox="0 0 24 24" fill="none" stroke="#fff" stroke-width="2" stroke-linejoin="round"><rect x="2" y="5" width="20" height="14" rx="1"/><path d="M2 6l10 7 10-7"/></svg>
      <span>www.veltrano.co</span>
    </li>
  </ul>

  <div class="address">1840 Harbor Ln. Suite 310 Portland, OR 97209</div>
</section>

</body>
</html>
```